Berufora Banner Design (Profilbanner und Unternehmensbanner) (1584 x 396) (1128 x 191)
Zielgruppe
Ich bin Dienstleister und Unternehmensberater für technischen B2B Vertrieb.
Für meinen BeruFora Account suche ich einen Banner für meine Profilseite und einen Banner für die Unternehmensseite). Meine Zielgruppe sind leitende Angestellte in Unternehmen. Das Design sollte entsprechend grafisch hochwertig, seriös gestaltet sein.
I am a service provider and management consultant for technical B2B sales.
For my BeruFora account, I'm looking for a banner for my profile page and a banner for the company page). My target group are executives in companies. The design should have a correspondingly high-quality graphic design and be serious.
Aufgabenstellung
Wichtig ist die Berücksichtigung meines Logos (PNG im Anhang) und des Corporate Identity Farben (PDF Anhang und unten stehend). Stock Bilder oder Grafiken können/sollen gerne mit eingebunden werden. Wichtig ist hier der passende Gesamteindruck.
It is important to consider my logo (PNG in the attachment) and the corporate identity colors (PDF attachment and below). Stock images or graphics can/should be included. The right overall impression is important here.
HEX / HTML 002854
HEX / HTML 00b6e3
Bannergrößen / Banner sizes
Profilbanner (1584 x 396)
Unternehmensseitenbanner (1128 x 191)

```html
<!DOCTYPE html>
<html lang="de">
<head>
<meta charset="utf-8">
<title>Jorin Veltkamp Management &amp; Sales Consulting – Unternehmensseite</title>
<link href="https://fonts.googleapis.com/css2?family=Titillium+Web:wght@300;400;600;700&family=Source+Sans+3:wght@400;600&display=swap" rel="stylesheet">
<style>
  :root {
    --navy: #002854;
    --cyan: #00b6e3;
    --banner-deep: #02086e;
    --banner-mid: #0a22c8;
    --banner-bright: #0a6cf0;
    --logo-bg: #18304f;
    --ink: #1f1f1f;
    --muted: #666666;
    --meta: #7a7a7a;
    --action: #0a66c2;
    --white: #ffffff;
    --line-grey: #8c8c8c;
  }
  * { box-sizing: border-box; margin: 0; padding: 0; }
  html, body { width: 1200px; height: 656px; overflow: hidden; background: var(--white); }
  .page { position: relative; width: 1200px; height: 656px; font-family: "Source Sans 3", Arial, sans-serif; }

  .banner {
    position: absolute; left: 0; top: 0; width: 1200px; height: 303px; overflow: hidden;
    background: linear-gradient(100deg, var(--banner-bright) 0%, var(--banner-mid) 30%, var(--banner-deep) 70%, #010540 100%);
  }
  .banner-chevrons { position: absolute; left: 0; top: 0; }
  .banner-engine {
    position: absolute; left: 712px; top: 0; width: 488px; height: 303px;
    background: radial-gradient(ellipse at 45% 55%, #c9ccd3 0%, #6f737c 30%, #2a2c33 60%, rgba(2,8,110,0) 85%);
  }
  .headline {
    position: absolute; color: var(--white); font-family: "Titillium Web", Arial, sans-serif;
    font-size: 44px; line-height: 1; letter-spacing: 0.2px; white-space: nowrap;
  }
  .headline .light { font-weight: 300; font-size: 35px; }
  .headline strong { font-weight: 700; }
  .headline-one { left: 351px; top: 73px; }
  .headline-two { left: 390px; top: 125px; }

  .contact {
    position: absolute; top: 264px; display: flex; align-items: center; gap: 9px;
    color: var(--white); font-family: "Titillium Web", Arial, sans-serif; font-size: 15.5px; font-weight: 600;
  }
  .contact-phone { left: 232px; }
  .contact-web { left: 400px; }

  .logo-box {
    position: absolute; left: 39px; top: 213px; width: 166px; height: 165px; background: var(--logo-bg);
    display: flex; align-items: center; justify-content: center; text-align: center;
    color: var(--cyan); font-family: "Titillium Web", Arial, sans-serif; font-weight: 700; font-size: 20px; line-height: 1.15;
  }

  .company-name { position: absolute; left: 35px; top: 394px; font-size: 41px; font-weight: 400; color: var(--ink); white-space: nowrap; line-height: 1.2; }
  .tagline { position: absolute; left: 35px; top: 444px; font-size: 26px; color: #333; line-height: 1.2; }
  .meta { position: absolute; left: 34px; top: 477px; font-size: 23px; color: var(--meta); white-space: nowrap; line-height: 1.2; }
  .staff-link { position: absolute; left: 35px; top: 522px; font-size: 26px; font-weight: 600; color: var(--muted); line-height: 1.2; }

  .btn {
    position: absolute; top: 583px; height: 49px; border-radius: 25px;
    display: flex; align-items: center; justify-content: center; gap: 10px;
    font-size: 27px; font-weight: 600;
  }
  .btn-follow { left: 35px; width: 210px; background: var(--action); color: var(--white); }
  .btn-site { left: 258px; width: 292px; border: 1.5px solid var(--action); color: var(--action); background: var(--white); font-weight: 400; }
  .btn-more { left: 563px; width: 110px; border: 1.5px solid var(--line-grey); color: var(--muted); background: var(--white); font-weight: 400; }
</style>
</head>
<body>
<div class="page">
  <header class="banner">
    <svg class="banner-chevrons" width="1200" height="303" viewBox="0 0 1200 303">
      <polygon points="0,0 190,0 520,303 330,303" fill="#1a8cff" opacity="0.35"/>
      <polygon points="120,0 260,0 560,303 420,303" fill="#0b3ee0" opacity="0.55"/>
      <polygon points="60,0 80,0 380,303 360,303" fill="#5cc8ff" opacity="0.55"/>
      <polygon points="0,60 0,0 20,0 320,303 300,303" fill="#0a4cf2" opacity="0.3"/>
    </svg>
    <div class="banner-engine" role="img" aria-label="Foto eines Automotors mit Riemenscheiben und Keilriemen"></div>

    <p class="headline headline-one"><span class="light">VOLLE </span><strong>POWER</strong></p>
    <p class="headline headline-two"><span class="light">FÜR IHR </span><strong>BUSINESS</strong><span class="light">.</span></p>

    <div class="contact contact-phone">
      <svg width="22" height="22" viewBox="0 0 24 24" fill="none" stroke="#fff" stroke-width="1.5" stroke-linejoin="round">
        <path d="M5 3h4l2 5-2.5 1.5a11 11 0 0 0 6 6L16 13l5 2v4a2 2 0 0 1-2 2A16 16 0 0 1 3 5a2 2 0 0 1 2-2z"/>
      </svg>
      <span>0123 | 987 654 0</span>
    </div>
    <div class="contact contact-web">
      <svg width="22" height="22" viewBox="0 0 24 24" fill="none" stroke="#fff" stroke-width="1.4">
        <circle cx="12" cy="12" r="10"/><ellipse cx="12" cy="12" rx="4.5" ry="10"/>
        <line x1="2" y1="12" x2="22" y2="12"/><path d="M4 6.5h16M4 17.5h16"/>
      </svg>
      <span>JORINVELTKAMP.DE</span>
    </div>
  </header>

  <div class="logo-box">Jorin<br>Veltkamp</div>

  <h1 class="company-name">Jorin Veltkamp Management &amp; Sales Consulting GmbH</h1>
  <p class="tagline">B2B Sales Consulting</p>
  <p class="meta">Business Consulting und Unternehmensdienstleistungen · Bad Lindenau, North Rhine-Westphalia · 1 Follower</p>
  <p class="staff-link">1 Mitarbeiter:in auf BeruFora ansehen</p>

  <div class="btn btn-follow">
    <svg width="22" height="22" viewBox="0 0 20 20" stroke="#fff" stroke-width="3"><path d="M10 1v18M1 10h18"/></svg>
    <span>Folgen</span>
  </div>
  <div class="btn btn-site">
    <span>Website besuchen</span>
    <svg width="24" height="24" viewBox="0 0 24 24" fill="none" stroke="#0a66c2" stroke-width="2.6" stroke-linejoin="round">
      <path d="M14 3h7v7M21 3l-10 10"/><path d="M18 14v6H4V6h6"/>
    </svg>
  </div>
  <div class="btn btn-more"><span>Mehr</span></div>
</div>
</body>
</html>
```